Website Homepage Design

Tarvento Care Partners Inc. is a Canadian financial services company that specialize in the delivery and administration of alternative health benefit solutions. Tarvento is seeking to adjust their brand and develop a new website.

We like the design and layout of the website below but are not looking for an exact replica (be creative):

http://www.quellaroforum.example/

We want the colour scheme to be clean white and "fresh green", possibly with orange accents (links).

This posting is only for a website homepage design (no coding), but anyone who includes a new logo, in addition to the design, will get priority.

Best of luck,

Orrin
Updates

Project is guaranteed.

Please let me know if you are currently working on a design.

Thank you,

Orrin

*Update:

Two example websites with good colour scheme/design:

- http://blimeden.example/
- http://www.faltrukidscove.example.au/

I have attached a wireframe and colour scheme to the project brief. The main colour should be the green one. Other colours can be used for highlights and accents, etc.

Target Market(s)

Business owners age 50+

Industry/Entity Type

Financial

Requirements
Must have
• - Clear and simple design
- Area for video (similar to http://www.quellaroforum.example)
Should not have
• - Lots of pictures

```html
<!DOCTYPE html>
<html lang="en">
<head>
<meta charset="utf-8">
<title>Tarvento Care Partners — Home</title>
<link rel="stylesheet" href="https://fonts.googleapis.com/css2?family=Arimo:wght@400;700&family=Oswald:wght@500;700&family=Crimson+Text&family=Cormorant+Garamond:ital,wght@1,500&family=Open+Sans:wght@400;600&display=swap">
<style>
:root{
  --orange:#f47c0b;
  --green:#5aae7c;
  --green-dark:#3f8d5f;
  --text:#666;
  --rule:#e4e6e5;
  --band:#f6f8f7;
  --black:#111;
}
*{margin:0;padding:0;box-sizing:border-box}
html,body{width:1200px;height:1019px;overflow:hidden;background:#fff}
body{position:relative;font-family:Arimo,Arial,sans-serif;color:var(--text)}
.abs{position:absolute}
.top-bar{left:0;top:0;width:1200px;height:3px;background:var(--orange)}
.login{left:983px;top:14px;width:100px;height:34px;border-radius:4px;background:linear-gradient(#6cc08f,var(--green-dark));color:#fff;font-weight:700;font-size:14px;display:flex;align-items:center;justify-content:center;border:1px solid #3a7f56}
.brand{left:145px;top:50px;display:flex;align-items:center;gap:7px}
.brand-name{font-size:34px;color:var(--orange);font-weight:400;letter-spacing:-0.5px}
.brand-dot{width:11px;height:11px;border-radius:50%;background:var(--green)}
.tagline{left:306px;top:69px;font-family:"Crimson Text",serif;font-size:14px;color:#777}
.tagline .e{color:var(--orange)} .tagline .a{color:var(--green)}
.nav{right:118px;top:69px;display:flex;font-size:13.5px;color:#777}
.nav span{padding:0 8px;border-left:1px solid #ddd}
.nav span:first-child{border-left:none}
.nav span:last-child{padding-right:0}
.rule{height:1px;background:linear-gradient(90deg,transparent,var(--rule) 20%,var(--rule) 80%,transparent)}
.hero-media{left:122px;top:143px}
.pitch{left:729px;top:229px;font-family:Oswald,sans-serif;color:#555;line-height:1;white-space:nowrap}
.pitch .l1{font-size:15.5px;font-weight:500;line-height:18px}
.pitch .l2{font-size:21.5px;font-weight:500;line-height:24px;margin-top:1px}
.pitch .big{display:flex;align-items:baseline;gap:9px;font-size:72px;font-weight:700;line-height:64px;margin-top:6px;letter-spacing:-1px}
.pitch .big .c{color:var(--orange)}
.pitch .big .in{font-family:Arimo,sans-serif;font-weight:400;font-size:38px;letter-spacing:0;color:#555}
.pitch .big .h{color:var(--green)}
.cta{left:732px;top:354px;width:198px;height:52px;border-radius:5px;background:linear-gradient(#3a3a3a,var(--black));color:#fff;font-family:"Open Sans",sans-serif;font-size:21px;display:flex;align-items:center;justify-content:center}
.call{left:732px;top:416px;width:202px;text-align:center;font-size:17px;color:#222}
.card{top:545px;width:282px;height:95px;background:linear-gradient(180deg,#fcfdfc,#f3f6f4);border-radius:4px;box-shadow:0 8px 10px -8px rgba(0,0,0,.12);text-align:center}
.card .t{font-size:18px;color:var(--orange);margin-top:12px}
.card .s{font-family:"Crimson Text",serif;font-size:22px;color:#555}
.card .m{position:absolute;right:36px;bottom:14px;font-family:"Open Sans",sans-serif;font-size:14px;color:#555;display:flex;align-items:center;gap:6px}
.card .m i{width:9px;height:12px;border-radius:50% 50% 40% 40%;background:var(--green);display:inline-block}
.quote{left:163px;top:719px}
.quote-text{left:185px;top:752px;width:300px;font-family:"Cormorant Garamond",serif;font-style:italic;font-size:30px;line-height:30px;color:#666}
.quote-text b{font-size:46px;line-height:0;color:#aaa;font-weight:500}
.quote-by{left:383px;top:914px;font-family:"Open Sans",sans-serif;font-size:12.5px;font-weight:600;color:#555}
.col{top:736px;font-family:"Open Sans",sans-serif}
.col h3{font-size:17px;font-weight:400;color:#666;margin-bottom:2px}
.col li{list-style:none;font-size:12px;line-height:20px;color:#777}
.col .live{color:var(--green-dark)}
.badge{top:888px;height:36px;background:#cfd2d0}
.foot{left:0;top:958px;width:1200px;height:61px;background:var(--band)}
.copy{left:131px;top:980px;font-family:"Open Sans",sans-serif;font-size:11px;color:#777}
.follow{left:916px;top:980px;font-family:"Open Sans",sans-serif;font-size:12px;color:#666;display:flex;align-items:center;gap:5px}
.follow i{width:16px;height:16px;display:inline-block;border-radius:2px}
</style>
</head>
<body>
<div class="abs top-bar"></div>
<div class="abs login">Login | Join</div>
<div class="abs brand"><span class="brand-name">Tarvento</span><span class="brand-dot"></span></div>
<div class="abs tagline">We make it <span class="e">easy.</span> We make it <span class="a">affordable.</span></div>
<nav class="abs nav"><span>Small Business</span><span>Big Business</span><span>Broker Business</span><span>Our Company</span><span>Contact Us</span></nav>
<div class="abs rule" style="left:270px;top:105px;width:690px"></div>

<svg class="abs hero-media" width="620" height="345" viewBox="0 0 620 345" role="img" aria-label="Laptop showing the introductory video with a play button">
  <defs>
    <linearGradient id="lid" x1="0" y1="0" x2="0" y2="1"><stop offset="0" stop-color="#e6e6e6"/><stop offset="1" stop-color="#c4c4c4"/></linearGradient>
    <linearGradient id="base" x1="0" y1="0" x2="0" y2="1"><stop offset="0" stop-color="#d8d8d8"/><stop offset="1" stop-color="#a9a9a9"/></linearGradient>
  </defs>
  <path d="M83 312 V14 Q83 2 97 2 H528 Q542 2 542 14 V312 Z" fill="url(#lid)"/>
  <path d="M2 311 H618 Q618 322 600 327 H20 Q2 322 2 311 Z" fill="url(#base)"/>
</svg>
<div class="abs pitch">
  <div class="l1">As a Sole Proprietor, Professional or Small Business Owner,</div>
  <div class="l2">you have the option to cut your healthcare</div>
  <div class="big"><span class="c">CO$T</span><span class="in">in</span><span class="h">Half!</span></div>
</div>
<div class="abs cta">Get Started Now</div>
<div class="abs call">Call: 1-800-555-0142</div>
<div class="abs rule" style="left:270px;top:500px;width:690px"></div>

<div class="abs card" style="left:152px"><div class="t">Reduce Costs</div><div class="s">Calculate Your Savings</div><div class="m">Learn More <i></i></div></div>
<div class="abs card" style="left:460px"><div class="t">How it works</div><div class="s">View Brochure</div><div class="m" style="right:60px">Learn More <i></i></div></div>
<div class="abs card" style="left:768px"><div class="t">Questions?</div><div class="s">Contact us today</div><div class="m" style="right:50px">Learn More <i></i></div></div>
<div class="abs rule" style="left:380px;top:683px;width:500px"></div>

<svg class="abs quote" width="340" height="195" viewBox="0 0 340 195">
  <path d="M22 1 H322 Q336 1 336 15 V125 Q336 148 300 149 H250 L227 188 L238 149 H15 Q1 149 1 135 V40 Q1 1 22 1 Z" fill="#fafbfb" stroke="#cfd1d0" stroke-width="1.2"/>
</svg>
<div class="abs quote-text"><b>“</b> Truely amazing. This is exactly what each financial services should be offering.</div>
<div class="abs quote-by">– Guest Customer</div>

<div class="abs col" style="left:568px"><h3>Menu</h3><ul><li>Small Business</li><li>Big Business</li><li>Broker Business</li><li>Our Company</li><li>Contact Us</li></ul></div>
<div class="abs col" style="left:720px"><h3>Who We Are</h3><ul><li>About Us</li><li>Meet the Team</li><li>News</li><li>Careers</li></ul></div>
<div class="abs col" style="left:877px"><h3>Customer Service</h3><ul><li class="live">Click for Live Help!</li><li>Call us at 1-800-555-0142</li><li>Email: info@tarvento.example</li></ul></div>

<div class="abs badge" style="left:760px;width:114px;border-radius:3px"></div>
<div class="abs badge" style="left:881px;width:42px;border-radius:50%"></div>
<div class="abs badge" style="left:937px;width:24px;border-radius:2px"></div>
<div class="abs badge" style="left:970px;width:70px;border-radius:18px"></div>

<div class="abs foot"></div>
<div class="abs copy">Copyright © 2010 Hollis Brook Consulting Group Inc. Ver. 1.0.298</div>
<div class="abs follow">Follow us <i style="background:#5a74ae"></i><i style="background:#6cb8dc"></i><i style="background:#c8302b"></i></div>
</body>
</html>
```